ORU professional cleaner

this professional multi-surface cleaner is intended for professionals.
Powerful degreaser. We would like to focus on the professional side.
We already have a range of disinfectants, and we would like a design close to this range but still distinct. The name is ORU and yhe logo is MOXAglow.the visible part of the label is 55mm and will be affixed to a round bottle with trigger .

Target Market(s)

professional

```html
<!DOCTYPE html>
<html lang="en">
<head>
<meta charset="utf-8">
<title>ORU Professional Multi-surface Cleaner Label</title>
<link href="https://fonts.googleapis.com/css2?family=Barlow+Condensed:wght@700&family=Fira+Sans+Extra+Condensed:wght@300;400;600&family=Nunito:wght@600&display=swap" rel="stylesheet">
<style>
  :root {
    --page-bg: #f5f5f5;
    --band-green: #2b8c43;
    --band-green-dark: #1f7d35;
    --brand-green: #3cb44a;
    --outline-green: #1f7d35;
    --sky-blue: #86c9ec;
    --pale-blue: #d8ecf9;
    --white: #ffffff;
    --ink: #1d1d1d;
    --logo-green: #4cc35a;
  }
  * { margin: 0; padding: 0; box-sizing: border-box; }
  html, body {
    width: 900px;
    height: 1200px;
    overflow: hidden;
    background: var(--page-bg);
  }
  .label {
    position: absolute;
    left: 212px;
    top: 46px;
    width: 475px;
    height: 1107px;
    overflow: hidden;
    background: linear-gradient(180deg, var(--sky-blue) 8%, var(--pale-blue) 38%, var(--white) 62%, var(--white) 100%);
  }
  .range-band {
    position: absolute;
    left: 0; top: 0;
    width: 100%;
    height: 97px;
    background: var(--band-green);
    display: flex;
    align-items: center;
    justify-content: center;
  }
  .range-band__title {
    font-family: "Fira Sans Extra Condensed", sans-serif;
    font-weight: 600;
    font-size: 58px;
    letter-spacing: 0.5px;
    color: var(--white);
    padding-top: 4px;
  }
  .usage-icon {
    position: absolute;
    left: 348px;
    top: 125px;
    width: 104px;
    height: 104px;
    border-radius: 22px;
    background: var(--band-green-dark);
    border: 4px solid var(--white);
    transform: rotate(-12deg);
  }
  .product-name {
    position: absolute;
    left: 44px;
    top: 196px;
    font-family: "Barlow Condensed", sans-serif;
    font-weight: 700;
    font-size: 245px;
    line-height: 1;
    color: var(--brand-green);
    -webkit-text-stroke: 4px var(--white);
    paint-order: stroke fill;
    text-shadow: 0 0 1px var(--outline-green), 0 0 2px var(--outline-green);
  }
  .descriptions {
    position: absolute;
    left: 53px;
    top: 428px;
    font-family: "Fira Sans Extra Condensed", sans-serif;
    font-weight: 300;
    font-size: 40px;
    line-height: 40px;
    color: var(--ink);
  }
  .descriptions__item { margin-bottom: 18px; }
  .descriptions__lang { font-weight: 400; font-size: 34px; }
  .brand-footer {
    position: absolute;
    left: 0;
    top: 830px;
    width: 475px;
    height: 277px;
  }
  .brand-footer__wave { position: absolute; inset: 0; }
  .brand-mark {
    position: absolute;
    left: 0;
    top: 92px;
    width: 100%;
    display: flex;
    flex-direction: column;
    align-items: center;
    gap: 14px;
  }
  .brand-mark__dot {
    width: 64px;
    height: 64px;
    border-radius: 50%;
    background: var(--logo-green);
  }
  .brand-mark__name {
    font-family: "Nunito", sans-serif;
    font-weight: 600;
    font-size: 54px;
    line-height: 1;
    color: var(--white);
  }
</style>
</head>
<body>
  <main class="label">
    <header class="range-band">
      <span class="range-band__title">PROFESSIONAL</span>
    </header>

    <div class="usage-icon" role="img" aria-label="Icon of a hand wiping a surface with a cloth"></div>

    <h1 class="product-name">ORU</h1>

    <div class="descriptions">
      <p class="descriptions__item">Multi-surface<br>cleaner <span class="descriptions__lang">FR</span></p>
      <p class="descriptions__item">Multi-surface<br>cleaner</p>
      <p class="descriptions__item">Multi-surface<br>cleaner <span class="descriptions__lang">DE</span></p>
    </div>

    <footer class="brand-footer">
      <svg class="brand-footer__wave" width="475" height="277" viewBox="0 0 475 277" aria-hidden="true">
        <path d="M0 32 C40 12 70 0 97 0 C150 0 185 55 232 55 C285 55 320 0 382 0 C420 0 450 10 475 25 L475 277 L0 277 Z" fill="var(--band-green)"/>
      </svg>
      <div class="brand-mark">
        <span class="brand-mark__dot"></span>
        <span class="brand-mark__name">MOXAglow</span>
      </div>
    </footer>
  </main>
</body>
</html>
```